Thornbury Building Company - Card Design

I am looking to use the logo designs that you already did for me to develop a business card. I would like the card to have a black background and be double sided. I want white and green logo and text. I have attached an inspiration photo of a look that I like. I would like to use the Vertical Logo attached to take up the full front side of the card. On the back where I have my name and information, I would like to have the horizontal logo or maybe even just the image of the 'A' and trees without the text. I am open, but I am looking for something clean and simple and I want the green to really pop! Additional files can be found under Design #: 58302946

Target Market(s)

Homeowners

Industry/Entity Type

Construction

Contact Information for Business Card

Name: Marcus Thornbury, Title: Project Manager, Phone: 555.274.8136, Email: thornburybuildingcompany@mailvesta.com, address: 487 Larkspur Ln, Cedar Hollow, OR 95033, Lic# 2468317

Colors
00AB8E
00BBA5
67D7C9
C6EFE9
E9F9F6

Requirements
Nice to have
• I would like to see the logos that I have already got from ArtLoomHub, though I am open to new ones

```html
<!DOCTYPE html>
<html lang="en">
<head>
<meta charset="utf-8">
<title>Thornbury Building Company – Business Card</title>
<link rel="stylesheet" href="https://fonts.googleapis.com/css2?family=Montserrat:wght@400;500;700&display=swap">
<style>
  :root {
    --stage: #2b2b2b;
    --card-front: #262626;
    --card-back: #1c1c1c;
    --green: #6cb846;
    --white: #ffffff;
    --text: #f2f2f2;
  }
  * { margin: 0; padding: 0; box-sizing: border-box; }
  html, body { width: 1200px; height: 1059px; overflow: hidden; }
  body {
    background: var(--stage);
    font-family: "Montserrat", sans-serif;
    position: relative;
  }
  .card {
    position: absolute;
    border-radius: 18px;
    box-shadow: 0 14px 30px rgba(0,0,0,0.55);
    overflow: hidden;
  }
  .card-front {
    left: 257px; top: 89px; width: 687px; height: 390px;
    background: var(--card-front);
  }
  .card-back {
    left: 254px; top: 547px; width: 693px; height: 393px;
    background: var(--card-back);
  }
  .front-brand {
    position: absolute; left: 0; right: 0; top: 168px;
    display: flex; align-items: center; justify-content: center; gap: 16px;
  }
  .brand-square {
    width: 44px; height: 44px; background: var(--green); flex: none;
  }
  .brand-name {
    color: var(--white); font-weight: 700; text-transform: uppercase;
    letter-spacing: 1px; line-height: 1.05;
  }
  .front-brand .brand-name { font-size: 30px; }
  .back-brand {
    position: absolute; left: 38px; top: 150px; width: 230px;
    display: flex; flex-direction: column; align-items: center; gap: 14px;
    text-align: center;
  }
  .back-brand .brand-square { width: 40px; height: 40px; }
  .back-brand .brand-name { font-size: 21px; }
  .divider {
    position: absolute; left: 298px; top: 109px; width: 2px; height: 176px;
    background: var(--green);
  }
  .contact { position: absolute; left: 320px; top: 100px; color: var(--text); }
  .contact-name {
    color: var(--green); font-weight: 700; font-size: 25px; letter-spacing: 0.8px;
    line-height: 30px;
  }
  .contact-title { font-size: 16px; line-height: 20px; margin-bottom: 24px; }
  .contact-license { color: var(--green); font-size: 15px; line-height: 22px; }
  .contact-address { font-size: 15px; line-height: 22px; margin-bottom: 22px; }
  .contact-line {
    display: flex; align-items: center; gap: 7px; font-size: 15px; line-height: 28px;
  }
  .contact-line svg { width: 13px; height: 13px; flex: none; fill: var(--green); }
</style>
</head>
<body>
  <section class="card card-front">
    <div class="front-brand">
      <span class="brand-square"></span>
      <span class="brand-name">Thornbury<br>Building Company</span>
    </div>
  </section>

  <section class="card card-back">
    <div class="back-brand">
      <span class="brand-square"></span>
      <span class="brand-name">Thornbury<br>Building<br>Company</span>
    </div>
    <div class="divider"></div>
    <div class="contact">
      <p class="contact-name">MARCUS THORNBURY</p>
      <p class="contact-title">Project Manager</p>
      <p class="contact-license">Lic# 2468317</p>
      <p class="contact-address">487 Larkspur Ln, Cedar Hollow, OR 95033</p>
      <p class="contact-line">
        <svg viewBox="0 0 24 24" aria-hidden="true"><path d="M6.6 10.8a15.1 15.1 0 0 0 6.6 6.6l2.2-2.2c.3-.3.7-.4 1-.2 1.1.4 2.3.6 3.6.6.6 0 1 .4 1 1V20c0 .6-.4 1-1 1C10.6 21 3 13.4 3 4c0-.6.4-1 1-1h3.5c.6 0 1 .4 1 1 0 1.3.2 2.5.6 3.6.1.3 0 .7-.2 1z"/></svg>
        555.274.8136
      </p>
      <p class="contact-line">
        <svg viewBox="0 0 24 24" aria-hidden="true"><path d="M2 5h20v2l-10 6L2 7z M2 9l10 6 10-6v10H2z"/></svg>
        thornburybuildingcompany@mailvesta.com
      </p>
    </div>
  </section>
</body>
</html>
```